Combat Sports news website design

Redesigning our existing website to make it more modern, responsive and suitable for our needs. The design needs to take in to account all aspects of our current website structure and services. View the existing website at https://www.ringpulse.co.nz

Particular attention should be paid to our livestream service, which is growing and needs to be much more user friendly to the current experience.

The homepage, article listings and article pages need designs.

Target Market(s)

Combat sports fans

Industry/Entity Type

Media

Coding

Coded - Design and coding required

Number of Pages Required

5+ page

Font styles to use
Sans Serif

Requirements
Must have
• All the functionality of the existing website must be taken in to account, and improved upon.
New design must incorporate our existing logo/colour scheme as this has only just been designed.

```html
<!DOCTYPE html>
<html lang="en">
<head>
<meta charset="utf-8">
<title>Ring Pulse – Boxing</title>
<link href="https://fonts.googleapis.com/css2?family=Montserrat:wght@400;500;600;700&family=Oswald:wght@500;600;700&display=swap" rel="stylesheet">
<style>
:root{
  --red:#b3121b;
  --ink:#1d1d1f;
  --nav:#26262a;
  --subnav:#37373b;
  --panel:#f2f2f2;
  --muted:#555;
  --footer:#2d2d30;
  --field:#4a4a4e;
  --ad:#c4c4c4;
}
*{box-sizing:border-box;margin:0;padding:0}
html,body{width:1200px;height:3657px;overflow:hidden}
body{position:relative;background:#fff;font-family:"Montserrat",sans-serif;color:var(--ink)}
.abs{position:absolute}
/* header */
.topnav{left:0;top:0;width:1200px;height:60px;background:var(--nav);font-family:"Oswald",sans-serif;color:#fff;font-size:14px;font-weight:600;text-transform:uppercase}
.topnav span{position:absolute;top:20px;letter-spacing:.2px}
.topnav .active{font-size:17px;top:17px}
.topnav .active::after{content:"";position:absolute;left:-20px;right:-20px;top:39px;height:3px;background:var(--red)}
.brand{left:560px;top:10px;font-family:"Oswald",sans-serif;font-weight:700;font-size:18px;line-height:18px;color:#fff;text-align:center;width:80px}
.subnav{left:0;top:60px;width:1200px;height:48px;background:var(--subnav);font-family:"Oswald",sans-serif;font-size:13px;font-weight:600;color:#9a9a9e;text-transform:uppercase}
.subnav span{position:absolute;top:15px}
.subnav .on{color:#fff}
/* hero */
.hero{left:0;top:108px;width:1200px;height:514px;background:radial-gradient(ellipse at 55% 20%,#4a3a34 0%,#221c1c 45%,#121012 100%)}
.hero-title{left:210px;top:238px;width:760px;font-size:42px;line-height:51px;font-weight:700;color:#fff;text-transform:uppercase}
.hero-more{left:210px;top:402px;font-size:16px;color:#fff;letter-spacing:1px;font-weight:500}
/* section */
.section-title{left:115px;top:704px;font-size:20px;font-weight:700;letter-spacing:.5px;border-left:6px solid var(--red);padding-left:12px;line-height:26px}
.grid{left:115px;top:773px;width:640px;display:grid;grid-template-columns:298px 298px;column-gap:40px;grid-auto-rows:457px}
.card-img{width:298px;height:180px;background:linear-gradient(135deg,#3a3f7a,#1b1c2a 60%,#6b2a2a)}
.card-img.ring{background:linear-gradient(135deg,#2a2c3a,#5a5c6a 50%,#1d1e26)}
.card-img.poster{background:linear-gradient(180deg,#2b3a55,#1a2233 70%,#c7d14a 100%)}
.card-img.team{background:linear-gradient(135deg,#7a3a2c,#2a2a2e 55%,#5a5a5e)}
.card h3{margin:20px 6px 0;font-size:16px;line-height:20px;font-weight:700}
.card p{margin:12px 6px 0;font-size:11.5px;line-height:15px;color:var(--muted)}
.meta{margin:10px 6px 0;font-size:8px;letter-spacing:.6px;color:#444;text-transform:uppercase;display:flex;align-items:center;gap:6px;height:14px}
.meta+.meta{margin-top:6px}
.btn{display:inline-flex;align-items:center;gap:6px;margin:14px 6px 0;background:var(--red);color:#fff;font-size:9px;font-weight:600;letter-spacing:.8px;padding:0 16px;height:31px;text-transform:uppercase}
/* sidebar */
.panel{left:802px;width:298px;background:var(--panel);padding:24px 22px}
.panel h4{font-size:14px;font-weight:700;letter-spacing:.6px;border-left:5px solid var(--red);padding-left:11px;line-height:18px}
.head{margin-top:26px}
.head a{display:block;color:var(--red);font-size:13px;line-height:16px;text-decoration:none;letter-spacing:.3px}
.head .meta{margin:6px 0 0;font-size:7.5px}
.head li{list-style:none;margin-bottom:20px}
.ad{margin:24px 2px 0;height:162px;background:var(--ad)}
.follow{display:flex;flex-wrap:wrap;gap:13px;margin-top:20px}
.follow span{width:120px;height:32px;color:#fff;font-size:11px;font-weight:700;letter-spacing:.5px;display:flex;align-items:center;justify-content:center;gap:8px}
.follow i{width:12px;height:12px;border-radius:50%;background:#fff;display:inline-block}
.poll-q{margin:30px 4px 0;font-size:11.5px;font-weight:700;letter-spacing:.5px;line-height:15px}
.opt{display:flex;align-items:center;gap:17px;margin:20px 4px 0;font-size:11.5px;font-weight:700;letter-spacing:.6px;height:26px}
.radio{width:26px;height:26px;border-radius:50%;border:2px solid var(--red);display:flex;align-items:center;justify-content:center}
.radio.sel::after{content:"";width:14px;height:14px;border-radius:50%;background:var(--red)}
.poll-btns{display:flex;gap:11px;margin:34px 4px 0}
.poll-btns span{background:var(--red);color:#fff;font-size:10px;letter-spacing:.8px;height:32px;display:flex;align-items:center;padding:0 22px}
/* pagination */
.pager{left:0;top:3118px;width:1200px;height:32px;font-size:15px;font-weight:700;color:var(--red)}
.pager .prev{position:absolute;left:330px;top:6px}
.pager .next{position:absolute;left:755px;top:6px}
.pager .num{position:absolute;top:0;width:28px;height:32px;background:var(--red);color:#fff;font-size:13px;display:flex;align-items:center;justify-content:center}
.pager .num.cur{background:#111}
/* footer */
.footer{left:0;top:3247px;width:1200px;height:410px;background:var(--footer);color:#fff}
.f-brand{left:82px;top:28px;font-family:"Oswald",sans-serif;font-weight:700;font-size:44px;line-height:44px;color:#fff;display:flex;align-items:center;gap:10px}
.f-brand i{width:22px;height:22px;background:var(--red);display:inline-block}
.f-name{left:82px;top:155px;font-size:18px;font-weight:700;color:#d8d8d8}
.f-bio{left:82px;top:180px;width:243px;font-size:12.5px;line-height:15px;color:#a9a9ad;text-align:justify;font-family:Arial,sans-serif}
.f-head{font-size:12px;color:#6d6d71;letter-spacing:.4px;text-transform:uppercase}
.f-list{font-size:13.5px;line-height:22px;color:#e6e6e6;list-style:none;margin-top:6px}
.f-icons{left:452px;top:306px;display:flex;gap:38px}
.f-icons i{width:18px;height:18px;border-radius:50%;background:#d0d0d0;display:block}
.field{width:180px;height:22px;background:var(--field);font-size:8px;color:#ddd;padding:7px 9px;margin-bottom:9px}
.copy{left:82px;top:382px;font-size:8px;color:#a9a9ad;font-family:Arial,sans-serif}
.help{left:452px;top:376px;font-size:13px;color:#6d6d71;display:flex;align-items:center;gap:10px}
.help b{font-weight:400;color:#e6e6e6}
</style>
</head>
<body>

<header>
  <nav class="abs topnav">
    <span style="left:136px">Home</span>
    <span class="active" style="left:244px">Categories</span>
    <span style="left:389px">Live events</span>
    <span style="left:744px">Contact us</span>
    <span style="left:853px">About us</span>
    <span style="left:959px">Login&nbsp;&nbsp;/&nbsp;&nbsp;Register</span>
    <svg class="abs" style="left:1096px;top:20px" width="19" height="19" viewBox="0 0 19 19" fill="none" stroke="#fff" stroke-width="2"><circle cx="8" cy="8" r="6"/><path d="M12.5 12.5L17.5 17.5"/></svg>
  </nav>
  <div class="abs brand">RING<br>PULSE</div>
  <nav class="abs subnav">
    <span style="left:136px">MMA</span>
    <span class="on" style="left:197px">Kickboxing</span>
    <span style="left:294px">Boxing</span>
    <span style="left:365px">Wrestling</span>
    <span style="left:458px">XFW</span>
    <span style="left:512px">PACFC</span>
  </nav>
</header>

<section class="abs hero" role="img" aria-label="Photo of a boxer in red gloves against a dark background"></section>
<h1 class="abs hero-title">Kahu Dellman steps into Summit 80kg division on short notice</h1>
<div class="abs hero-more">READ MORE &nbsp;→</div>

<h2 class="abs section-title">BOXING</h2>

<main class="abs grid">
  <article class="card"><div class="card-img" role="img" aria-label="Winning team with championship belts in the ring"></div><h3>Tane Whitford predicts hard fight at Summit this Saturday</h3><p>Tane Whitford is a 20-year-old Muay Thai phenom fighting out of New Plymouth, Taranaki....</p><div class="meta">◷ 12:00PM &nbsp;WED 28 APR</div><div class="meta">◉ COLE HARLAND</div><span class="btn">Read more →</span></article>
  <article class="card"><div class="card-img" role="img" aria-label="Two fighters exchanging punches under coloured lights"></div><h3>Tane Whitford predicts hard fight at Summit this Saturday</h3><p>Tane Whitford is a 20-year-old Muay Thai phenom fighting out of New Plymouth, Taranaki....</p><div class="meta">◷ 12:00PM &nbsp;WED 28 APR</div><div class="meta">◉ COLE HARLAND</div><span class="btn">Read more →</span></article>
  <article class="card"><div class="card-img ring" role="img" aria-label="Referee raising the winner's arm in the ring"></div><h3>Tane Whitford predicts hard fight at Summit this Saturday</h3><p>Tane Whitford is a 20-year-old Muay Thai phenom fighting out of New Plymouth, Taranaki....</p><div class="meta">◷ 12:00PM &nbsp;WED 28 APR</div><div class="meta">◉ COLE HARLAND</div><span class="btn">Read more →</span></article>
  <article class="card"><div class="card-img ring" role="img" aria-label="Two fighters clinching in a dim arena"></div><h3>Tane Whitford predicts hard fight at Summit this Saturday</h3><p>Tane Whitford is a 20-year-old Muay Thai phenom fighting out of New Plymouth, Taranaki....</p><div class="meta">◷ 12:00PM &nbsp;WED 28 APR</div><div class="meta">◉ COLE HARLAND</div><span class="btn">Read more →</span></article>
  <article class="card"><div class="card-img poster" role="img" aria-label="Event poster for a Muay Thai warrior series"></div><h3>Tane Whitford predicts hard fight at Summit this Saturday</h3><p>Tane Whitford is a 20-year-old Muay Thai phenom fighting out of New Plymouth, Taranaki....</p><div class="meta">◷ 12:00PM &nbsp;WED 28 APR</div><div class="meta">◉ COLE HARLAND</div><span class="btn">Read more →</span></article>
  <article class="card"><div class="card-img team" role="img" aria-label="Fight team group photo in a gym"></div><h3>Tane Whitford predicts hard fight at Summit this Saturday</h3><p>Tane Whitford is a 20-year-old Muay Thai phenom fighting out of New Plymouth, Taranaki....</p><div class="meta">◷ 12:00PM &nbsp;WED 28 APR</div><div class="meta">◉ COLE HARLAND</div><span class="btn">Read more →</span></article>
  <article class="card"><div class="card-img ring" role="img" aria-label="Referee raising the winner's arm in the ring"></div><h3>Tane Whitford predicts hard fight at Summit this Saturday</h3><p>Tane Whitford is a 20-year-old Muay Thai phenom fighting out of New Plymouth, Taranaki....</p><div class="meta">◷ 12:00PM &nbsp;WED 28 APR</div><div class="meta">◉ COLE HARLAND</div><span class="btn">Read more →</span></article>
  <article class="card"><div class="card-img ring" role="img" aria-label="Two fighters clinching in a dim arena"></div><h3>Tane Whitford predicts hard fight at Summit this Saturday</h3><p>Tane Whitford is a 20-year-old Muay Thai phenom fighting out of New Plymouth, Taranaki....</p><div class="meta">◷ 12:00PM &nbsp;WED 28 APR</div><div class="meta">◉ COLE HARLAND</div><span class="btn">Read more →</span></article>
  <article class="card"><div class="card-img poster" role="img" aria-label="Event poster for a Muay Thai warrior series"></div><h3>Tane Whitford predicts hard fight at Summit this Saturday</h3><p>Tane Whitford is a 20-year-old Muay Thai phenom fighting out of New Plymouth, Taranaki....</p><div class="meta">◷ 12:00PM &nbsp;WED 28 APR</div><div class="meta">◉ COLE HARLAND</div><span class="btn">Read more →</span></article>
  <article class="card"><div class="card-img team" role="img" aria-label="Fight team group photo in a gym"></div><h3>Tane Whitford predicts hard fight at Summit this Saturday</h3><p>Tane Whitford is a 20-year-old Muay Thai phenom fighting out of New Plymouth, Taranaki....</p><div class="meta">◷ 12:00PM &nbsp;WED 28 APR</div><div class="meta">◉ COLE HARLAND</div><span class="btn">Read more →</span></article>
</main>

<aside>
  <section class="abs panel" style="top:773px;height:580px">
    <h4>LATEST HEADLINES</h4>
    <ul class="head">
      <li><a>Jono Macrae looking to avenge her only loss</a><div class="meta">◷ 12:00PM &nbsp;WED 28 APR</div></li>
      <li><a>Kahu Dellman steps into Summit 80kg division on short notice</a><div class="meta">◷ 12:00PM &nbsp;WED 28 APR</div></li>
      <li><a>Five GKL New Zealand Cup winners crowned at Forged to Fight 9</a><div class="meta">◷ 12:00PM &nbsp;WED 28 APR</div></li>
      <li><a>Tane Whitford predicts hard fight at Summit this Saturday</a><div class="meta">◷ 12:00PM &nbsp;WED 28 APR</div></li>
      <li><a>Unbroken Fight Series 2 results</a><div class="meta">◷ 12:00PM &nbsp;WED 28 APR</div></li>
      <li><a>VIDEO: “I’m bringing pain!” - Dane Okoro declares war on Sam Teale</a><div class="meta">◷ 12:00PM &nbsp;WED 28 APR</div></li>
    </ul>
  </section>
  <section class="abs panel" style="top:1385px;height:246px"><h4>ADVERTISEMENT</h4><div class="ad" role="img" aria-label="Advertisement space"></div></section>
  <section class="abs panel" style="top:1660px;height:173px">
    <h4>FOLLOW US</h4>
    <div class="follow">
      <span style="background:#7a3aa8"><i></i>FOLLOW</span>
      <span style="background:#1d9bf0"><i></i>FOLLOW</span>
      <span style="background:#2f4f8f"><i></i>FOLLOW</span>
    </div>
  </section>
  <section class="abs panel" style="top:1862px;height:246px"><h4>ADVERTISEMENT</h4><div class="ad" role="img" aria-label="Advertisement space"></div></section>
  <section class="abs panel" style="top:2136px;height:402px">
    <h4>OPINION POLL</h4>
    <div class="poll-q">WHAT COMBAT SPORT DO YOU PREFER?</div>
    <div class="opt" style="margin-top:28px"><span class="radio sel"></span>MMA</div>
    <div class="opt"><span class="radio"></span>WRESTLING</div>
    <div class="opt"><span class="radio"></span>KICKBOXING</div>
    <div class="opt"><span class="radio"></span>MUAY THAI</div>
    <div class="opt"><span class="radio"></span>ALL OF THE ABOVE</div>
    <div class="poll-btns"><span>VOTE</span><span>SHOW RESULTS</span></div>
  </section>
</aside>

<nav class="abs pager">
  <span class="prev">← &nbsp;PREV</span>
  <span class="num" style="left:502px">1</span>
  <span class="num cur" style="left:545px">2</span>
  <span class="num" style="left:588px">3</span>
  <span class="num" style="left:630px">4</span>
  <span class="next">NEXT &nbsp;→</span>
</nav>

<footer class="abs footer">
  <div class="abs f-brand"><i></i>RING PULSE</div>
  <div class="abs f-name">Marina Foulkes</div>
  <p class="abs f-bio">Marina has worked in the media industry since she was 15-years-old. She has worked in both radio and print, and is the co-founder and editor-in-chief of Ring Pulse. As well as being the Ring Pulse Editor, she focuses on writing for multi-discipline combat sports.</p>
  <div class="abs" style="left:452px;top:42px"><div class="f-head">Site map</div><ul class="f-list"><li>Home</li><li>MMA</li><li>Kickboxing</li><li>Boxing</li><li>Wrestling</li><li>XFW</li><li>PACFC</li><li>Live events</li></ul></div>
  <div class="abs" style="left:613px;top:42px"><div class="f-head">Usefull links</div><ul class="f-list"><li>Site Terms</li><li>Advertisement</li><li>Contact us</li><li>Privacy</li></ul></div>
  <div class="abs f-head" style="left:452px;top:282px">Get in touch</div>
  <div class="abs f-icons"><i></i><i></i><i></i><i></i></div>
  <div class="abs" style="left:858px;top:42px">
    <div class="f-head" style="margin-bottom:8px">Contact us</div>
    <div class="field">First name</div>
    <div class="field">Last name</div>
    <div class="field">Email</div>
    <div class="field">Phone / Mobile</div>
    <div class="field" style="width:259px;height:150px">Message</div>
    <div style="width:96px;height:26px;background:var(--red);color:#fff;font-size:12px;display:flex;align-items:center;justify-content:center;margin-top:5px">Submit</div>
  </div>
  <div class="abs copy">Copyright © 2021-2022 RING PULSE All Rights Reserved</div>
  <div class="abs help">NEED HELP?
    <svg width="22" height="16" viewBox="0 0 22 16" fill="none" stroke="#d0d0d0" stroke-width="1.6"><rect x="1" y="1" width="20" height="14"/><path d="M1 1l10 8 10-8"/></svg>
    <b>newsdesk@ringpulse.co.nz</b></div>
</footer>

</body>
</html>
```